High end Electrical/home automation Business Card

Need a card for a high end electrical and home automation company utilising the existing logo.
Phone
Email
Website

Like black look with raised detail. Don’t necessarily need to keep colour of logo it could be made grayscale or white etc

Target Market(s)

High end clients

Contact Information for Business Card

Brightmoor Electrical

Requirements
Must have
• Logo, phone, email, website, address

High end look
Nice to have
• Black background card
Raised font
Should not have
• Lots of colour

```html
<!DOCTYPE html>
<html lang="en">
<head>
<meta charset="utf-8">
<title>Brightmoor Electrical – Business Card</title>
<link rel="stylesheet" href="https://fonts.googleapis.com/css2?family=Archivo:wght@600&family=Lato:wght@400;700&display=swap">
<style>
  :root {
    --backdrop: #2f2f2f;
    --card: #3a3a3a;
    --ink: #e8e8e8;
    --ink-soft: #d6d6d6;
  }
  * { box-sizing: border-box; margin: 0; padding: 0; }
  html, body { width: 1133px; height: 1200px; overflow: hidden; background: var(--backdrop); }
  .canvas { position: relative; width: 1133px; height: 1200px; }
  .card { position: absolute; background: var(--card); color: var(--ink); }
  .card-front { left: 248px; top: 190px; width: 654px; height: 359px; }
  .card-back { left: 242px; top: 624px; width: 660px; height: 365px; }

  .brand-name { font-family: "Archivo", sans-serif; font-weight: 600; color: var(--ink); white-space: nowrap; letter-spacing: -0.2px; }
  .front-brand { position: absolute; left: 38px; top: 48px; font-size: 27px; }

  .accent-bar { position: absolute; left: 5px; top: 154px; width: 7px; height: 38px; background: var(--ink); }
  .person { position: absolute; left: 37px; top: 154px; font-family: "Lato", sans-serif; }
  .person-name { font-size: 21px; font-weight: 400; letter-spacing: 0.3px; line-height: 1.1; }
  .person-title { font-size: 14px; color: var(--ink-soft); line-height: 1.2; }

  .address { position: absolute; left: 37px; top: 208px; font-family: "Lato", sans-serif; font-size: 14px; line-height: 17.6px; color: var(--ink-soft); }
  .contacts { position: absolute; left: 37px; top: 269px; list-style: none; font-family: "Lato", sans-serif; font-size: 14px; line-height: 17.6px; color: var(--ink-soft); }
  .contacts li { display: flex; align-items: center; gap: 7px; }
  .contacts svg { width: 11px; height: 11px; fill: var(--ink-soft); flex: none; }

  .front-mark { position: absolute; left: 330px; top: 30px; width: 300px; height: 310px; display: flex; flex-direction: column; align-items: center; justify-content: center; gap: 22px; }
  .front-mark .mark-dot { width: 150px; height: 150px; border-radius: 50%; background: var(--ink); }
  .front-mark .brand-name { font-size: 30px; }

  .back-lockup { position: absolute; left: 0; right: 0; top: 92px; display: flex; flex-direction: column; align-items: center; gap: 16px; }
  .back-lockup .mark-dot { width: 112px; height: 112px; border-radius: 50%; background: var(--ink); }
  .back-lockup .brand-name { font-size: 32px; }
</style>
</head>
<body>
<main class="canvas">
  <section class="card card-front" aria-label="Business card front">
    <h1 class="brand-name front-brand">Brightmoor Electrical</h1>
    <span class="accent-bar"></span>
    <div class="person">
      <p class="person-name">DANIEL HART</p>
      <p class="person-title">President</p>
    </div>
    <address class="address" style="font-style:normal">
      Brightmoor Electrical LLC<br>
      2140 Harbor View Road<br>
      Juneau, Alaska 99801
    </address>
    <ul class="contacts">
      <li><svg viewBox="0 0 24 24"><path d="M6.6 10.8a15 15 0 0 0 6.6 6.6l2.2-2.2a1 1 0 0 1 1-.25 11.4 11.4 0 0 0 3.6.57 1 1 0 0 1 1 1V20a1 1 0 0 1-1 1A17 17 0 0 1 3 4a1 1 0 0 1 1-1h3.5a1 1 0 0 1 1 1c0 1.25.2 2.45.57 3.57a1 1 0 0 1-.25 1z"/></svg>369-555-0142</li>
      <li><svg viewBox="0 0 24 24"><path d="M2 5h20v14H2z M3.5 6.5 12 12.5l8.5-6" fill="none" stroke="#d6d6d6" stroke-width="2.4"/></svg>info@brightmoorelectrical.com</li>
      <li><svg viewBox="0 0 24 24"><circle cx="12" cy="12" r="9" fill="none" stroke="#d6d6d6" stroke-width="2.4"/><path d="M3 12h18M12 3c3 3 3 15 0 18M12 3c-3 3-3 15 0 18" fill="none" stroke="#d6d6d6" stroke-width="1.8"/></svg>www.brightmoorelectrical.com</li>
    </ul>
    <div class="front-mark">
      <span class="mark-dot"></span>
      <span class="brand-name">Brightmoor</span>
    </div>
  </section>

  <section class="card card-back" aria-label="Business card back">
    <div class="back-lockup">
      <span class="mark-dot"></span>
      <span class="brand-name">Brightmoor Electrical</span>
    </div>
  </section>
</main>
</body>
</html>
```